BUSINESS CARD DESIGN

NAME- DALE VORSKIN
PHONE NUMER - 555- 714-9082
EMAIL- OFFICE@TRV-GROUNDMAKRZ.COM
BACK OF CARD- SPEACIALIZES IN LAND CLEARING, FORESTRY MUCLHING AND EXCAVATION

Contact Information for Business Card

NAME- DALE VORSKIN PHONE NUMER - 555- 714-9082 EMAIL- OFFICE@TRV-GROUNDMAKRZ.COM BACK OF CARD- SPEACIALIZES IN LAND CLEARING , MUCLHING AND EXCAVATION

```html
<!DOCTYPE html>
<html lang="en">
<head>
<meta charset="utf-8">
<title>Terravale Groundmakrz — Business Card</title>
<link rel="stylesheet" href="https://fonts.googleapis.com/css2?family=Montserrat:wght@400;500;700&display=swap">
<style>
  :root {
    --backdrop: #2e2e2e;
    --card-black: #070707;
    --card-white: #ffffff;
    --gold: #f5ad1c;
    --ink: #141414;
    --muted: #333333;
  }
  * { box-sizing: border-box; margin: 0; padding: 0; }
  html, body { width: 1200px; height: 1186px; overflow: hidden; }
  body {
    background: var(--backdrop);
    font-family: "Montserrat", sans-serif;
    position: relative;
  }
  .card {
    position: absolute;
    left: 250px;
    width: 700px;
    height: 400px;
    border-radius: 26px;
    overflow: hidden;
    box-shadow: 0 12px 30px rgba(0,0,0,.45);
  }
  .card--back { top: 110px; background: var(--card-black); }
  .card--front { top: 640px; background: var(--card-white); }

  /* brand block */
  .brand {
    position: absolute;
    display: flex;
    align-items: center;
    gap: 14px;
  }
  .brand__dot { width: 26px; height: 26px; border-radius: 50%; flex: none; }
  .brand__name { font-weight: 700; letter-spacing: 2px; line-height: 1.15; }

  /* back */
  .card--back .brand { left: 0; right: 0; top: 70px; flex-direction: column; gap: 16px; }
  .card--back .brand__dot { background: var(--gold); width: 34px; height: 34px; }
  .card--back .brand__name { color: var(--gold); font-size: 36px; text-align: center; }
  .rule { position: absolute; height: 2px; background: var(--gold); }
  .rule--wide { left: 190px; width: 320px; top: 272px; }
  .rule--narrow { left: 210px; width: 280px; top: 282px; }
  .back-phone {
    position: absolute; left: 0; right: 0; top: 298px;
    text-align: center; color: var(--gold);
    font-weight: 700; font-size: 22px; letter-spacing: 9px;
  }
  .services {
    position: absolute; left: 40px; right: 40px; top: 346px;
    text-align: center; color: var(--card-white);
    font-weight: 500; font-size: 13px; letter-spacing: 1px;
  }

  /* front */
  .card--front .brand { right: 60px; top: 60px; }
  .card--front .brand__dot { background: var(--ink); }
  .card--front .brand__name { color: var(--ink); font-size: 24px; }
  .front-phone-top {
    position: absolute; right: 60px; top: 132px;
    color: var(--ink); font-weight: 700; font-size: 14px; letter-spacing: 6px;
  }
  .divider { position: absolute; left: 40px; right: 40px; top: 200px; height: 2px; background: var(--gold); }
  .person { position: absolute; left: 40px; top: 222px; }
  .person__name { color: var(--gold); font-weight: 700; font-size: 30px; }
  .person__title { color: var(--muted); font-size: 16px; margin-top: 2px; }
  .contacts { position: absolute; left: 40px; top: 300px; list-style: none; }
  .contacts li {
    display: flex; align-items: center; gap: 12px;
    color: var(--ink); font-size: 16px; font-weight: 500; margin-bottom: 8px;
  }
  .contacts svg { width: 16px; height: 16px; flex: none; }
  .address {
    position: absolute; right: 40px; top: 228px;
    text-align: right; color: var(--ink); font-size: 15px; line-height: 1.4;
  }
  .band { position: absolute; bottom: 0; height: 44px; }
  .band--black { right: 200px; width: 60px; background: var(--ink); clip-path: polygon(30% 0, 100% 0, 100% 100%, 0 100%); }
  .band--gold { right: 0; width: 196px; background: var(--gold); }
</style>
</head>
<body>
  <section class="card card--back" aria-label="Card back">
    <div class="brand">
      <span class="brand__dot"></span>
      <span class="brand__name">TERRAVALE<br>GROUNDMAKRZ LLC<br>OHIO</span>
    </div>
    <div class="rule rule--wide"></div>
    <div class="rule rule--narrow"></div>
    <p class="back-phone">555-714-9082</p>
    <p class="services">SPECIALIZES IN LAND CLEARING, FORESTRY MULCHING &amp; EXCAVATION</p>
  </section>

  <section class="card card--front" aria-label="Card front">
    <div class="brand">
      <span class="brand__dot"></span>
      <span class="brand__name">TERRAVALE<br>GROUNDMAKRZ LLC</span>
    </div>
    <p class="front-phone-top">555-714-9082</p>
    <div class="divider"></div>
    <div class="person">
      <p class="person__name">DALE VORSKIN</p>
      <p class="person__title">Managing Director</p>
    </div>
    <ul class="contacts">
      <li>
        <svg viewBox="0 0 16 16"><path fill="var(--gold)" d="M3 1l3 3-1.5 2a9 9 0 0 0 5.5 5.5L12 10l3 3-2 2C7 15 1 9 1 3z"/></svg>
        555- 714-9082
      </li>
      <li>
        <svg viewBox="0 0 16 16"><rect x="1" y="3" width="14" height="10" rx="1" fill="var(--gold)"/><path d="M1 4l7 5 7-5" stroke="#fff" stroke-width="1.3" fill="none"/></svg>
        OFFICE@TRV-GROUNDMAKRZ.COM
      </li>
      <li>
        <svg viewBox="0 0 16 16"><circle cx="8" cy="8" r="7" fill="var(--gold)"/><path d="M1 8h14M8 1c3 3 3 11 0 14M8 1c-3 3-3 11 0 14" stroke="#fff" stroke-width="1" fill="none"/></svg>
        WWW.TRV-GROUNDMAKRZ.COM
      </li>
    </ul>
    <p class="address">418 Harbor Ridge Rd, #112<br>Millbrook, OH 430417</p>
    <div class="band band--black"></div>
    <div class="band band--gold"></div>
  </section>
</body>
</html>
```